*YO!!! Designers Needed!!* Front Page Cover Needed for a $$Billion Dollar$$ Company

We are a manufacturer of aluminum electrolytic capacitors. We are looking to create a front page cover that will be used on our annual report. We are a publicly listed company and work with many Meridex 400 companies, so your work will be viewed by the BIG GUNS and EXECUTIVES around the WORLD! If selected, you may be selected for additional work.

The front page cover should be unique. If elegance, modern, bling, and creativity somehow got together and had a child, that's what the cover page would look like!

Inspired Examples attached. Check them out!

www.brovanta.com

Font styles to use
Sans Serif

Requirements
Must have
• 1. Must include the attached logo. Logo size, color, and placement are at your discretion.

2. Should include the text, '2020 Annual Report'

3. The design should incorporate the use of foil and/or be embossed. The foil can be part of the design or can be the full page. See various examples attached for reference.

4. Shall be in A4 size and vertical orientation.
Nice to have
• Feel free to add any icons or stock photos (for example capacitors or circuit boards) if needed.

Be creative here and don't be afraid to be bold! The end product will be printed and budget is not a limiting factor, so feel free to make it extravagant if needed.

Our slogan is "Plan Forward". This slogan can or cannot be part of the theme.

```html
<!DOCTYPE html>
<html lang="en">
<head>
<meta charset="UTF-8">
<title>Brovanta Annual Report 2020 Cover</title>
<link href="https://fonts.googleapis.com/css2?family=Josefin+Sans:wght@400;700&display=swap" rel="stylesheet">
<style>
  :root {
    --backdrop: #ecebea;
    --cover-black: #1f1f1f;
    --cover-edge: #151515;
    --band-grey: #dcdcdc;
    --band-grey-light: #e6e6e6;
    --ink: #1c1c1c;
    --foil-gold: #c39a2c;
  }
  html, body {
    margin: 0;
    padding: 0;
    width: 1200px;
    height: 900px;
    overflow: hidden;
    background: var(--backdrop);
  }
  .canvas {
    position: relative;
    width: 1200px;
    height: 900px;
  }
  .cover {
    position: absolute;
    left: 310px;
    top: 40px;
    width: 584px;
    height: 820px;
    background: var(--cover-black);
    border-left: 8px solid var(--cover-edge);
    box-sizing: border-box;
    border-radius: 2px;
    overflow: hidden;
  }
  .circuit-pattern {
    position: absolute;
    left: 0;
    bottom: 0;
    width: 100%;
    height: 500px;
  }
  .title-band {
    position: absolute;
    left: 166px;
    top: 0;
    width: 234px;
    height: 435px;
    background: linear-gradient(180deg, var(--band-grey-light), var(--band-grey));
    font-family: "Josefin Sans", sans-serif;
    color: var(--ink);
  }
  .report-title {
    position: absolute;
    left: 0;
    top: 38px;
    width: 100%;
    margin: 0;
    text-align: center;
    font-weight: 700;
    font-size: 52px;
    line-height: 62px;
    letter-spacing: 0.5px;
  }
  .report-title span { display: block; }
  .foil-rule {
    position: absolute;
    left: 26px;
    top: 268px;
    width: 182px;
    height: 11px;
    background: var(--foil-gold);
  }
  .brand {
    position: absolute;
    left: 26px;
    top: 318px;
    width: 182px;
  }
  .brand-name {
    display: block;
    text-align: center;
    font-weight: 700;
    font-size: 40px;
    line-height: 48px;
    letter-spacing: 0.5px;
  }
  .brand-tagline {
    display: block;
    text-align: right;
    font-weight: 400;
    font-size: 12px;
    letter-spacing: 0.8px;
    margin-top: 4px;
  }
</style>
</head>
<body>
  <main class="canvas">
    <section class="cover">
      <svg class="circuit-pattern" role="img" aria-label="Gold foil circuit-board traces rising from the bottom edge" viewBox="0 0 576 500" preserveAspectRatio="none">
        <defs>
          <linearGradient id="circuitFade" x1="0" y1="0" x2="0" y2="1">
            <stop offset="0" stop-color="#1f1f1f" stop-opacity="0"/>
            <stop offset="0.55" stop-color="#3a2a14" stop-opacity="0.6"/>
            <stop offset="1" stop-color="#8a5a1a" stop-opacity="0.75"/>
          </linearGradient>
        </defs>
        <rect x="0" y="0" width="576" height="500" fill="url(#circuitFade)"/>
      </svg>
      <div class="title-band">
        <h1 class="report-title">
          <span>ANUAL</span>
          <span>REPORT</span>
          <span>2020</span>
        </h1>
        <div class="foil-rule"></div>
        <div class="brand">
          <span class="brand-name">Brovanta</span>
          <span class="brand-tagline">PLAN FORWARD.</span>
        </div>
      </div>
    </section>
  </main>
</body>
</html>
```